Tiny Meadow Product Label for Tear-Free Head-to-Toe Wash

Need a bottle label design for a new line of natural products targeting infants and children. Products are Pediatrician-developed and paraben-free, sulfate-free, fragrance-free, and cruelty-free. Design should be clean and have a high-end feel to it. Will need other product labels in Tiny Meadow line designed as well in upcoming projects.

Target Market(s)

Newborn to young elementary age children and their parents

Industry/Entity Type

Cosmetics/Beauty

Font styles to use
Other font styles liked:
• Brand fonts are Jost and Sonorous

Colors

Designer to choose colors to be used in the design.

Requirements
Must have
• Tiny Meadow logo, Pediatrician Developed logo, and a clean high-end feel to it. The label must fit the specialty bottle we will be using (label measurements and diagram will be provided) for the front and back of bottle only (NOT the side labels). It must include our list of ingredients (will provide once designer selected).
Nice to have
• Should stand out on the shelf of other baby products due to it's clean simplicity and high-end feel
Should not have
• too much of a "kiddie" feel to it (targeting the parents not the kids)

```html
<!DOCTYPE html>
<html lang="en">
<head>
<meta charset="utf-8">
<title>Tiny Meadow – Tear-Free Head-to-Toe Wash Label</title>
<link rel="stylesheet" href="https://fonts.googleapis.com/css2?family=Rubik:wght@800&family=Jost:wght@500;600&family=Arimo:ital,wght@0,400;1,700&display=swap">
<style>
  :root {
    --canvas: #ecebe8;
    --label: #faf8f6;
    --ink: #222222;
    --gold: #98722c;
    --dieline: #7db4d8;
    --white: #ffffff;
  }
  * { margin: 0; padding: 0; box-sizing: border-box; }
  html, body {
    width: 1200px; height: 1200px; overflow: hidden;
    background: var(--canvas);
  }
  .sheet { position: relative; width: 1200px; height: 1200px; }
  .label {
    position: absolute; top: 269px;
    width: 460px; height: 662px;
    background: var(--label);
    border-radius: 50% 50% 0 0 / 92px 92px 0 0;
  }
  .label--front { left: 100px; border: 1px solid var(--dieline); }
  .label--back { left: 640px; }

  /* Front */
  .brand {
    position: absolute; left: 32px; top: 112px;
    display: flex; align-items: center; gap: 14px;
  }
  .brand__dot {
    width: 60px; height: 60px; border-radius: 50%;
    border: 2px solid var(--gold);
  }
  .brand__name {
    font-family: "Jost", sans-serif; font-weight: 600;
    font-size: 25px; color: var(--ink); letter-spacing: 0.5px; line-height: 1;
  }
  .product-title {
    position: absolute; left: 29px; top: 236px;
    font-family: "Rubik", sans-serif; font-weight: 800;
    font-size: 66px; line-height: 62px; color: var(--ink);
    letter-spacing: -0.5px;
  }
  .claim-band {
    position: absolute; left: 0; top: 440px;
    width: 416px; height: 40px;
    background: var(--gold); color: var(--white);
    border-radius: 0 20px 20px 0;
    font-family: "Jost", sans-serif; font-weight: 500; font-size: 22.5px;
    display: flex; align-items: center; padding-left: 29px;
  }
  .free-badges {
    position: absolute; left: 25px; top: 525px;
    display: flex; gap: 15px;
  }
  .free-badge {
    width: 74px; height: 74px; border-radius: 50%;
    border: 1.5px dashed var(--ink); opacity: 0.75;
  }
  .net-weight {
    position: absolute; left: 29px; top: 611px;
    font-family: "Jost", sans-serif; font-weight: 600;
    font-size: 22.5px; color: var(--gold);
  }

  /* Back */
  .back-copy {
    position: absolute; left: 62px; top: 106px; width: 336px;
    font-family: "Arimo", sans-serif; font-size: 17px; line-height: 23.5px;
    color: var(--ink);
  }
  .back-copy .line {
    display: block; text-align: justify; text-align-last: justify;
  }
  .back-copy .line--last { text-align-last: left; }
  .back-copy h2 {
    font-family: "Arimo", sans-serif; font-style: italic; font-weight: 700;
    font-size: 23px; line-height: 28px; color: var(--gold); margin: 8px 0 4px;
  }
  .maker {
    position: absolute; left: 62px; top: 554px;
    font-family: "Arimo", sans-serif; font-size: 17px; line-height: 23.5px;
    color: var(--ink);
  }
  .maker__heading { font-style: italic; font-weight: 700; color: var(--gold); }
  .pediatric-badge {
    position: absolute; left: 324px; top: 546px;
    width: 84px; height: 84px; border-radius: 50%;
    border: 2px solid var(--gold);
  }
</style>
</head>
<body>
<main class="sheet">
  <section class="label label--front" aria-label="Front label">
    <div class="brand">
      <span class="brand__dot"></span>
      <span class="brand__name">Tiny Meadow</span>
    </div>
    <h1 class="product-title">Tear-Free<br>Head-to-<br>Toe Wash</h1>
    <div class="claim-band">Naturally formulated for delicate skin</div>
    <div class="free-badges">
      <span class="free-badge" role="img" aria-label="Paraben free badge"></span>
      <span class="free-badge" role="img" aria-label="Sulfate free badge"></span>
      <span class="free-badge" role="img" aria-label="Fragrance free badge"></span>
      <span class="free-badge" role="img" aria-label="Cruelty free badge"></span>
    </div>
    <p class="net-weight">Net wt: 73 mL/2,43 fl.oz</p>
  </section>

  <section class="label label--back" aria-label="Back label">
    <div class="back-copy">
      <p>
        <span class="line">A gentle, all-in-one cleanser made with</span>
        <span class="line">natural ingredients to protect and</span>
        <span class="line">nourish baby’s delicate hair and skin.</span>
        <span class="line">Pediatrician-developed and suitable</span>
        <span class="line line--last">for daily use from newborn onwards.</span>
      </p>
      <h2>Directions:</h2>
      <p>
        <span class="line">Dispense a small amount into hands or</span>
        <span class="line">washcloth. Gently massage into wet</span>
        <span class="line">hair and skin. Rinse thoroughly. Avoid</span>
        <span class="line line--last">contact with eyes.</span>
      </p>
      <h2>Ingredients:</h2>
      <p>
        <span class="line">Aqua, Glycerin, Decyl Glucoside,</span>
        <span class="line">Sodium Lauroyl Lactylate, Coco-</span>
        <span class="line">Glucoside, Glyceryl Oleate, Xanthan</span>
        <span class="line line--last">Gum, Sodium Benzoate, Citric Acid.</span>
        <span class="line line--last">(Full list to be finalized.)</span>
      </p>
    </div>
    <div class="maker">
      <div class="maker__heading">Manufactured for</div>
      <div>Tiny Meadow Co.</div>
      <div>tinymeadow.com/Made in USA</div>
    </div>
    <span class="pediatric-badge" role="img" aria-label="Pediatrician developed badge"></span>
  </section>
</main>
</body>
</html>
```